New website: Wanderfjordia.com

We need to build a website for our small travel agency.
We want to be able to upload our brochures and offer our tours on site. No online payments involved yet.

We want to create an exact copy of another website: www.trekvalora.is, but with our own information and products. We like that design very much.

We are not going to do any sales via the website as the website above, but instead we want to show in the same style and everything the different tours that we offer.

We need to be able to modify tours: tour pictures, info, add videos, text, etc.

We need the website in English and Spanish. We can provide the Spanish translation.

We would advice you to create a copy of that website, with the text to be editable by us.
We own the website www.wanderfjordia.com and need that the designer uploads it and makes it work as well.

We have uploaded some pictures that can be used as place markers.

I HAVE UPLOADED OUR BROCHURE DEMO SO YOU CAN GET MORE INFO IN ENGLISH ABOUT US AND MORE PICTURES.

PLEASE REMEMBER THAT THE WEBSITE ¨MOVES¨ when you resize it! Specially the pictures get ¨bigger¨ or smaller¨ when you resize. The same applies to the logos :-)

Once you have created the front page just as the original website I will select it and then we can put the real info and extra pages :-)

Tourists, international people traveling.

Tourism

Coded - Design and coding required

5+ page

Sans Serif

ffffff

• Exactly the same layout of the website mentioned (www.trekvalora.is)
• Everything the same, but with our own logo, texts and photos.
• HOME
• TOURS
• GROUPS
• OUR MOST POPULAR TOURS

```html
<!DOCTYPE html>
<html lang="en">
<head>
<meta charset="utf-8">
<title>Wanderfjordia — Home</title>
<link rel="stylesheet" href="https://fonts.googleapis.com/css2?family=Raleway:wght@400;500;600;700&family=Open+Sans:wght@400;600&display=swap">
<style>
:root{
  --red:#d7262b;
  --ink:#2b2b2b;
  --muted:#8a8a8a;
  --body:#666666;
  --line:#e3e3e3;
  --band:#efefef;
  --footer:#3b3b3b;
  --white:#ffffff;
}
*{box-sizing:border-box;margin:0;padding:0}
html,body{width:1200px;height:3689px;overflow:hidden;background:var(--white)}
body{position:relative;font-family:"Raleway",sans-serif;color:var(--ink)}
.abs{position:absolute}

/* header */
.site-header{position:absolute;left:0;top:0;width:1200px;height:126px;border-bottom:4px solid var(--red);background:var(--white)}
.brand{position:absolute;left:74px;top:17px;width:104px;height:104px;border-radius:50%;background:#111;display:flex;align-items:center;justify-content:center;color:var(--white);font-weight:700;font-size:13px;letter-spacing:.2px}
.main-nav a{position:absolute;top:66px;font-family:"Open Sans",sans-serif;font-size:13px;font-weight:600;color:#333;text-decoration:none;letter-spacing:.4px}
.main-nav a.active{color:var(--red)}
.nav-underline{position:absolute;left:412px;top:92px;width:96px;height:3px;background:var(--red)}

/* hero */
.hero-tile{position:absolute;overflow:hidden}
.hero-caption{position:absolute;color:var(--white)}
.hero-caption .title{font-size:46px;font-weight:500;line-height:1}
.hero-caption .sub{font-size:31px;font-weight:500;line-height:1.2;margin-top:4px}

/* tours */
.section-title{position:absolute;left:0;width:1200px;text-align:center;font-size:26px;font-weight:600;letter-spacing:.5px}
.tour-tabs a{position:absolute;top:772px;font-family:"Open Sans",sans-serif;font-size:14px;color:#444;text-decoration:none}
.tour-tabs a.active{color:var(--red)}
.tabs-rule{position:absolute;left:76px;top:812px;width:1050px;height:1px;background:var(--line)}
.tabs-active{position:absolute;left:76px;top:810px;width:120px;height:4px;background:var(--red)}
.tour-card{position:absolute;width:330px}
.tour-card .photo{width:330px;height:248px}
.tour-card h3{margin-top:18px;font-size:22px;font-weight:500;color:var(--ink)}
.tour-card .kind{margin-top:8px;font-family:"Open Sans",sans-serif;font-size:15px;color:var(--muted)}
.tour-card .price{margin-top:12px;font-family:"Open Sans",sans-serif;font-size:16px;font-weight:600;color:var(--red)}
.btn-outline{position:absolute;border:2px solid var(--red);border-radius:26px;color:#333;font-family:"Open Sans",sans-serif;font-weight:600;font-size:14px;letter-spacing:.4px;display:flex;align-items:center;justify-content:center;text-decoration:none;background:var(--white)}

/* story bands */
.story{position:absolute;left:0;width:1200px;height:382px;background:var(--band);overflow:hidden}
.story .visual{position:absolute;top:0;height:382px}
.story .visual.left{left:0;width:700px;-webkit-mask-image:linear-gradient(90deg,#000 0%,#000 62%,transparent 100%);mask-image:linear-gradient(90deg,#000 0%,#000 62%,transparent 100%)}
.story .visual.right{left:400px;width:800px;-webkit-mask-image:linear-gradient(270deg,#000 0%,#000 68%,transparent 100%);mask-image:linear-gradient(270deg,#000 0%,#000 68%,transparent 100%)}
.story .copy{position:absolute;top:66px;width:510px}
.story h2{font-size:27px;font-weight:500;letter-spacing:.5px;color:var(--ink)}
.story p{margin-top:24px;font-family:"Open Sans",sans-serif;font-size:14px;line-height:29px;color:var(--body)}
.story .btn-outline{position:static;width:157px;height:48px;margin-top:28px}

/* contact strip */
.contact-strip{position:absolute;left:0;top:3295px;width:1200px;height:148px;background:var(--white)}
.contact-item{position:absolute;top:36px;display:flex;align-items:center;gap:28px;font-family:"Open Sans",sans-serif;font-size:16px;font-weight:600;color:#333;letter-spacing:.3px}
.ring{width:76px;height:76px;border-radius:50%;border:2px solid #555;display:flex;align-items:center;justify-content:center}

/* footer */
.site-footer{position:absolute;left:0;top:3443px;width:1200px;height:246px;background:var(--footer);color:var(--white)}
.footer-brand{position:absolute;left:74px;top:50px;width:148px;height:148px;border-radius:50%;background:#111;display:flex;align-items:center;justify-content:center;font-weight:700;font-size:19px;letter-spacing:.3px}
.footer-col{position:absolute;top:36px;font-family:"Open Sans",sans-serif;font-size:12px;line-height:29.5px;color:var(--white)}
.footer-col .head{font-weight:600}
.socials{position:absolute;left:910px;top:41px;display:flex;gap:8px}
.socials span{width:30px;height:30px;border-radius:50%;background:#8c8c8c}
.copyright{position:absolute;left:910px;top:100px;font-family:"Open Sans",sans-serif;font-size:12px;line-height:20px;color:#bdbdbd}
</style>
</head>
<body>

<header class="site-header">
  <div class="brand">Wanderfjordia</div>
  <nav class="main-nav">
    <svg class="abs" style="left:443px;top:32px" width="18" height="24" viewBox="0 0 18 24"><path d="M9 0C4 0 0 4 0 9c0 6 9 15 9 15s9-9 9-15c0-5-4-9-9-9z" fill="var(--red)"/><circle cx="9" cy="9" r="3.5" fill="#fff"/></svg>
    <a class="active" style="left:434px">HOME</a>
    <a style="left:511px">TOURS</a>
    <a style="left:594px">GROUPS</a>
    <a style="left:689px">RENT A CAR</a>
    <a style="left:805px">FLIGHT</a>
    <a style="left:889px">CONTACT</a>
    <svg class="abs" style="left:996px;top:66px" width="18" height="18" viewBox="0 0 18 18"><circle cx="7.5" cy="7.5" r="5.5" fill="none" stroke="#333" stroke-width="2.4"/><line x1="11.5" y1="11.5" x2="16.5" y2="16.5" stroke="#333" stroke-width="2.6" stroke-linecap="round"/></svg>
    <svg class="abs" style="left:1066px;top:67px" width="16" height="16" viewBox="0 0 16 16"><circle cx="8" cy="8" r="7" fill="none" stroke="#333" stroke-width="1.5"/><ellipse cx="8" cy="8" rx="3" ry="7" fill="none" stroke="#333" stroke-width="1.2"/><line x1="1" y1="8" x2="15" y2="8" stroke="#333" stroke-width="1.2"/></svg>
    <a style="left:1086px">EN</a>
    <svg class="abs" style="left:1110px;top:71px" width="10" height="7" viewBox="0 0 10 7"><polyline points="1,1 5,5 9,1" fill="none" stroke="#333" stroke-width="1.6"/></svg>
  </nav>
  <div class="nav-underline"></div>
</header>

<section class="hero">
  <div class="hero-tile" style="left:0;top:130px;width:600px;height:530px">
    <div role="img" aria-label="Hikers in a line crossing a snowy glacier ridge" style="width:100%;height:100%;background:linear-gradient(160deg,#c9dbe9 0%,#e8f0f6 40%,#a9c2d6 75%,#6f8fa8 100%)"></div>
    <div class="hero-caption" style="left:76px;top:425px"><div class="title">Lorem Euismod</div><div class="sub">Wanderfjordia</div></div>
  </div>
  <div class="hero-tile" style="left:605px;top:130px;width:595px;height:260px">
    <div role="img" aria-label="Mountain range above a turquoise lake" style="width:100%;height:100%;background:linear-gradient(180deg,#7fa6c9 0%,#8b7f72 45%,#5b8f8a 70%,#3f6b6a 100%)"></div>
    <div class="hero-caption" style="left:25px;top:155px"><div class="title">Lorem Euismod</div><div class="sub">Wanderfjordia</div></div>
  </div>
  <div class="hero-tile" style="left:605px;top:396px;width:595px;height:264px">
    <div role="img" aria-label="Jagged granite peaks over a blue lake with a wooden bench" style="width:100%;height:100%;background:linear-gradient(180deg,#5d86b4 0%,#b7c2cc 35%,#6b6f74 60%,#3c6c8c 100%)"></div>
    <div class="hero-caption" style="left:25px;top:155px"><div class="title">Lorem Euismod</div><div class="sub">Wanderfjordia</div></div>
  </div>
</section>

<section class="popular-tours">
  <h2 class="section-title" style="top:706px">OUR MOST POPULAR TOURS</h2>
  <nav class="tour-tabs">
    <a class="active" style="left:76px">Popular Tours</a>
    <a style="left:229px">Day Tours</a>
    <a style="left:352px">Travel by Air Tours</a>
    <a style="left:539px">Self Drive Tours</a>
    <a style="left:703px">Adventures Tours</a>
    <a style="left:883px">Customize Tours</a>
    <a style="left:1055px">Transfer</a>
  </nav>
  <div class="tabs-rule"></div>
  <div class="tabs-active"></div>

  <article class="tour-card" style="left:76px;top:846px">
    <div class="photo" role="img" aria-label="Lakeside lodge beneath cloudy skies and distant peaks" style="background:linear-gradient(180deg,#5f8fc4 0%,#c6d6e6 45%,#7e8e96 65%,#3f7f8f 100%)"></div>
    <h3>Lorem ipsum dolor sit</h3><div class="kind">Consectetuer</div><div class="price">6.400 ISK</div>
  </article>
  <article class="tour-card" style="left:435px;top:846px">
    <div class="photo" role="img" aria-label="Travellers looking at granite towers" style="background:linear-gradient(180deg,#4f7fb8 0%,#9aa3aa 45%,#5a5e5a 75%,#3a3d36 100%)"></div>
    <h3>Lorem ipsum dolor sit</h3><div class="kind">Consectetuer</div><div class="price">6.400 ISK</div>
  </article>
  <article class="tour-card" style="left:794px;top:846px">
    <div class="photo" role="img" aria-label="Open road across the steppe toward mountains" style="background:linear-gradient(180deg,#4d87c7 0%,#a9c3dc 50%,#6f7d5c 70%,#5a5a4a 100%)"></div>
    <h3>Lorem ipsum dolor sit</h3><div class="kind">Consectetuer</div><div class="price">6.400 ISK</div>
  </article>
  <article class="tour-card" style="left:76px;top:1239px">
    <div class="photo" role="img" aria-label="Dark lake under heavy clouds" style="background:linear-gradient(180deg,#6d7a86 0%,#b8bfc4 40%,#4c5a52 70%,#2f3b3a 100%)"></div>
    <h3>Lorem ipsum dolor sit</h3><div class="kind">Consectetuer</div><div class="price">6.400 ISK</div>
  </article>
  <article class="tour-card" style="left:435px;top:1239px">
    <div class="photo" role="img" aria-label="Mountains seen from a car window" style="background:linear-gradient(180deg,#3f78bf 0%,#d2dde6 40%,#6a6f6e 70%,#3a3c3c 100%)"></div>
    <h3>Lorem ipsum dolor sit</h3><div class="kind">Consectetuer</div><div class="price">6.400 ISK</div>
  </article>
  <article class="tour-card" style="left:794px;top:1239px">
    <div class="photo" role="img" aria-label="Off-road vehicle on a gravel plain" style="background:linear-gradient(180deg,#6f8aa5 0%,#c3c9cc 45%,#9a8b70 70%,#6f6450 100%)"></div>
    <h3>Lorem ipsum dolor sit</h3><div class="kind">Consectetuer</div><div class="price">6.400 ISK</div>
  </article>

  <a class="btn-outline" style="left:433px;top:1673px;width:334px;height:50px">VIEW ALL OUR POPULAR TOUR</a>
</section>

<section class="story" style="top:1770px">
  <div class="visual left" role="img" aria-label="Adult and child pointing toward snowy mountains" style="background:linear-gradient(180deg,#9cc0e0 0%,#c9d9e8 35%,#8f9a86 60%,#6b7d5a 100%)"></div>
  <div class="copy" style="left:612px">
    <h2>INTRODUCCION</h2>
    <p>Wanderfjordia es un nuevo tour operator receptivo de confianza especializado en el diseño y prestación de servicios personalizados de incoming en destinos prístinos de la Ecorregión Sub-Antártica y Antártica Chilena.</p>
    <a class="btn-outline">MORE INFO</a>
  </div>
</section>

<section class="story" style="top:2152px">
  <div class="visual right" role="img" aria-label="Boat passengers viewing a glacier face" style="background:linear-gradient(180deg,#6f9fd2 0%,#d9e6f0 40%,#8ca9c6 60%,#e8eef3 100%)"></div>
  <div class="copy" style="left:74px">
    <h2>QUIENES SOMOS</h2>
    <p>Somos una empresa conformada por un idóneo equipo de trabajo que consta de alta motivación, óptimo entrenamiento, elevado capital humano y cuyos integrantes poseen más de 10 años de experiencia trabajando en forma independiente...</p>
    <a class="btn-outline">MORE INFO</a>
  </div>
</section>

<section class="story" style="top:2533px">
  <div class="visual left" role="img" aria-label="Hiker with backpack by a mountain lake" style="background:linear-gradient(180deg,#7b9fc6 0%,#a08670 40%,#6a5a48 65%,#3f3a32 100%)"></div>
  <div class="copy" style="left:612px">
    <h2>MISION</h2>
    <p>Nuestra misión es ofrecer servicios de Turismo Receptivo para la Región de Magallanes y Antártica Chilena que cumplan con las exigencias de calidad y valor humano que nuestros clientes solicitan.</p>
    <a class="btn-outline">MORE INFO</a>
  </div>
</section>

<section class="story" style="top:2914px">
  <div class="visual right" role="img" aria-label="Couple seated on a stony lakeshore facing snowy peaks" style="background:linear-gradient(180deg,#6f9ccd 0%,#c8d4de 35%,#5c7a92 55%,#7a7468 100%)"></div>
  <div class="copy" style="left:74px">
    <h2>VISION</h2>
    <p>Nuestra visión es crear una Plataforma de Servicios Logísticos y Turísticos para la Ecorregión Sub-Antártica y Antártica que una toda la oferta turística de la zona a través de una red local, nacional y global de proveedores...</p>
    <a class="btn-outline">MORE INFO</a>
  </div>
</section>

<section class="contact-strip">
  <div class="contact-item" style="left:74px">
    <div class="ring"><svg width="30" height="30" viewBox="0 0 30 30"><rect x="3" y="6" width="20" height="20" rx="2" fill="none" stroke="var(--red)" stroke-width="2.4"/><path d="M12 18l2-5 11-11 3 3-11 11z" fill="var(--red)"/></svg></div>
    <span>NEWSLETTER SIGN UP</span>
  </div>
  <div class="contact-item" style="left:466px">
    <div class="ring"><svg width="28" height="28" viewBox="0 0 24 24"><path d="M6.6 10.8a15 15 0 006.6 6.6l2.2-2.2a1 1 0 011-.25 11 11 0 003.6.6 1 1 0 011 1V20a1 1 0 01-1 1A17 17 0 013 4a1 1 0 011-1h3.5a1 1 0 011 1 11 11 0 00.6 3.6 1 1 0 01-.25 1z" fill="var(--red)"/></svg></div>
    <span>1-800-555-0142</span>
  </div>
  <div class="contact-item" style="left:798px">
    <div class="ring"><svg width="30" height="24" viewBox="0 0 30 24"><rect x="1" y="2" width="28" height="20" rx="2" fill="var(--red)"/><polyline points="2,4 15,14 28,4" fill="none" stroke="#fff" stroke-width="2"/></svg></div>
    <span>info@wanderfjordia.com</span>
  </div>
</section>

<footer class="site-footer">
  <div class="footer-brand">Wanderfjordia</div>
  <div class="footer-col" style="left:317px">HOME<br>TOURS<br>GROUPS<br>RENT A CAR<br>FLIGHT<br>CONTACT</div>
  <div class="footer-col" style="left:480px">HOW TO BOOK<br>BOOKING TERMS<br>PRIVACY POLICY</div>
  <div class="footer-col" style="left:661px">
    <div class="head">WANDERFJORDIA</div>
    <div style="line-height:20px;margin:4px 0 4px">4120 Larkfield<br>Road,Brenmoor, D07 42KT</div>
    <div>&#9742;&nbsp; 1-800-555-0142</div>
    <div>&#9993;&nbsp; info@wanderfjordia.com</div>
  </div>
  <div class="socials"><span></span><span></span><span></span><span></span><span></span><span></span></div>
  <div class="copyright">Copyright © 2016. CompanyName<br>All Right Reserved</div>
</footer>

</body>
</html>
```